Home Page Website Design

The Site width is 1000 px. I've attached a Balsamiq mockup as a design layout guide. The design needs to be flat and clean. Please stick to the pixel dimensions of the mock up as the site will be responsive. I've also attached the logos used on the mockup for positional purposes.

Colours to use: Black, Grey, Green (Logo tie in) & green complementary colours.

Green (Logo tie in)
White Background
Titles: Black (Roboto Bold 700)
Text: Dark Grey (Roboto Normal 400)

Look & Style Example
http://www.brindlowe.org.uk/

Type Face
Google Fonts - Roboto

These are just guidelines, please feel free to use you own creative judgment.

Thanks

```html
<!DOCTYPE html>
<html lang="en">
<head>
<meta charset="utf-8">
<title>Marlow Vale Teaching Alliance – Home</title>
<link href="https://fonts.googleapis.com/css2?family=Questrial&family=Arimo:wght@400;700&display=swap" rel="stylesheet">
<style>
:root{
  --green:#17b24a;
  --green-hero:#22c25a;
  --green-dark:#0e9a3c;
  --yellow:#f5c518;
  --nav:#2b2b2b;
  --panel:#e6e6e6;
  --panel-dark:#555;
  --btn:#6a6a6a;
  --text:#222;
  --text-soft:#444;
  --line:#888;
  --white:#fff;
}
*{box-sizing:border-box;margin:0;padding:0}
html,body{width:893px;height:1200px;overflow:hidden;background:var(--white)}
body{position:relative;font-family:"Arimo",Arial,sans-serif;color:var(--text);font-size:11px}
.abs{position:absolute}
.heading{font-family:"Questrial","Century Gothic",sans-serif;font-weight:400;color:#111}

/* header */
.brand{left:8px;top:30px;width:170px}
.brand-mark{display:flex;align-items:center;gap:8px}
.brand-square{width:22px;height:22px;background:var(--green)}
.brand-name{font-family:"Questrial",sans-serif;color:var(--green);font-size:15px;line-height:1.2}
.login{left:824px;top:2px;width:65px;height:21px;background:var(--green);color:var(--white);font-family:"Questrial",sans-serif;font-size:13px;text-align:center;line-height:21px}
.live-chat{left:530px;top:26px;width:62px;text-align:center;font-family:"Questrial",sans-serif;font-size:11px;color:#333}
.register{left:605px;top:25px;width:284px;height:61px;background:var(--panel-dark);padding:6px 11px}
.register h2{font-family:"Questrial",sans-serif;font-weight:400;color:var(--white);font-size:18px;line-height:1}
.register-row{display:flex;gap:12px;margin-top:6px}
.register-input{width:173px;height:21px;background:var(--white);font-size:12px;line-height:21px;padding-left:8px;color:#333}
.register-submit{width:73px;height:21px;background:#bdbdbd;font-size:12px;line-height:21px;text-align:center;color:#222}

/* nav */
.nav{left:3px;top:98px;width:888px;height:33px;background:var(--nav);display:flex;align-items:center;padding-left:18px}
.nav a{color:var(--white);text-decoration:none;font-size:11px;margin-right:23.5px}
.search{left:681px;top:104px;width:204px;height:22px;background:var(--white);font-size:11px;line-height:22px;padding-left:9px;color:#222}
.search svg{position:absolute;right:7px;top:4px}

/* hero */
.hero{left:3px;top:131px;width:888px;height:299px;background:linear-gradient(100deg,#6e8a5c 0%,#c9d3cf 35%,#e8edf1 55%,#b9c2c9 75%,#d8dde1 100%)}
.hero-box{left:12px;top:143px;width:343px;height:278px;background:var(--green-hero);padding:16px 17px;color:var(--white)}
.hero-box h1{font-family:"Questrial",sans-serif;font-weight:400;font-size:25px;line-height:1.1;margin-bottom:24px}
.hero-box p{font-size:11.6px;line-height:1.2}
.hero-btn{display:inline-block;margin-top:27px;background:var(--yellow);color:#222;font-size:12px;width:105px;height:29px;line-height:29px;text-align:center}

/* columns */
.col-title{font-size:22px;top:448px}
.welcome-box{left:4px;top:482px;width:284px;height:415px;background:var(--panel)}
.video{left:15px;top:492px;width:263px;height:164px;background:#000}
.video-bar{position:absolute;left:0;bottom:0;width:100%;height:20px;background:#1b1b1b;border-top:2px solid #444}
.welcome-text{left:17px;top:677px;width:262px;font-size:11px;line-height:1.18;color:var(--text)}

.training-box{left:306px;top:482px;width:284px;height:191px;border:1px solid var(--line);padding:13px 13px}
.training-item{height:29px;background:var(--panel);border:1px solid #c9c9c9;margin-bottom:4px;display:flex;align-items:center;justify-content:space-between;padding:0 10px 0 11px;font-size:12px;color:#222}
.news-box{left:306px;top:714px;width:284px;height:184px;border:1px solid var(--line);padding:20px 17px}
.news-item h3{font-family:"Arimo",sans-serif;font-weight:400;font-size:15px;color:#111;margin-bottom:5px}
.news-item p{font-size:10px;color:var(--text-soft);line-height:1.3}
.news-item + .news-item{margin-top:21px}

.courses-box{left:604px;top:482px;width:285px;height:415px;background:var(--panel);padding:20px 18px}
.course h3{font-family:"Arimo",sans-serif;font-weight:700;font-size:14px;line-height:1.05;color:#111;margin-bottom:8px}
.course p{font-size:10.5px;line-height:1.35;color:var(--text-soft)}
.course-foot{display:flex;align-items:center;gap:16px;margin-top:10px}
.places{color:var(--green);font-size:12px}
.book{width:55px;height:23px;background:var(--btn);color:var(--white);font-size:12px;line-height:23px;text-align:center}
.course{padding-bottom:14px;border-bottom:1px solid #999;margin-bottom:14px}
.course:last-of-type{border-bottom:none}
.course-nav{position:absolute;right:16px;bottom:14px;display:flex;gap:8px}

/* partners */
.partners{left:0;top:925px;width:893px;height:75px}
.badge{position:absolute}
.partner-bar{left:20px;top:1000px;width:854px;height:6px;background:#555}
.partner-shadow{left:20px;top:1006px;width:854px;height:14px;background:radial-gradient(ellipse at 5% 0,rgba(0,0,0,.28),transparent 60%),radial-gradient(ellipse at 95% 0,rgba(0,0,0,.28),transparent 60%)}

/* footer */
.footer-col{top:1061px;font-size:11.5px;line-height:1.22;color:#111}
.hub{left:721px;top:1062px;display:flex;align-items:center;gap:6px;width:100px}
.hub-square{width:14px;height:14px;background:var(--green)}
.hub-name{font-family:"Questrial",sans-serif;font-size:12px;color:#333;line-height:1.15}
.social{left:811px;top:1072px;font-size:10px;color:#888;line-height:1.4}
.copyright{left:728px;top:1130px;font-size:10px;color:#444;line-height:1.25}
</style>
</head>
<body>

<header>
  <div class="abs brand">
    <div class="brand-mark"><span class="brand-square"></span><span class="brand-name">Marlow Vale<br>Teaching Alliance</span></div>
  </div>
  <div class="abs login">Login</div>
  <div class="abs live-chat">
    <svg width="40" height="46" viewBox="0 0 40 46" aria-hidden="true">
      <rect x="4" y="6" width="32" height="22" rx="5" fill="#555"/>
      <path d="M12 28 L10 38 L20 28 Z" fill="#555"/>
      <circle cx="13" cy="17" r="2.5" fill="#fff"/><circle cx="20" cy="17" r="2.5" fill="#fff"/><circle cx="27" cy="17" r="2.5" fill="#fff"/>
    </svg>
    <div>Live Chat</div>
  </div>
  <div class="abs register">
    <h2>Register Now</h2>
    <div class="register-row"><div class="register-input">email address</div><div class="register-submit">Submit</div></div>
  </div>
</header>

<nav class="abs nav">
  <a>Home</a><a>About Us</a><a>Training &amp; Development</a><a>Benefits</a><a>Members</a><a>What's On</a><a>Contact us</a><a>News</a><a>Forum</a>
</nav>
<div class="abs search">search
  <svg width="14" height="14" viewBox="0 0 14 14" aria-hidden="true"><circle cx="5.5" cy="5.5" r="4.3" fill="none" stroke="#000" stroke-width="2"/><line x1="8.6" y1="8.6" x2="13" y2="13" stroke="#000" stroke-width="2.4"/></svg>
</div>

<div class="abs hero" role="img" aria-label="Photo of smiling teachers in an office looking at a tablet together"></div>
<section class="abs hero-box">
  <h1>New Teachers in Workshop</h1>
  <p>Lorem ipsum dolor sit amet, consectetur adipisicing elit, sed do eiusmod tempor incididunt ut labore et dolore magna aliqua. Ut enim ad minim veniam, quis nostrud exercitation ullamco laboris nisi ut aliquip ex ea commodo consequat. Duis aute irure dolor in reprehenderit in voluptate velit esse cillum dolore eu fugiat nulla pariatur. Excepteur sint occaecat cupidatat non proident, sunt in culpa qui officia deserunt mollit anim id est laborum.</p>
  <span class="hero-btn">Find Our More</span>
</section>

<!-- welcome -->
<h2 class="abs heading col-title" style="left:7px">Welcome</h2>
<div class="abs welcome-box"></div>
<div class="abs video" role="img" aria-label="Welcome video player">
  <div class="video-bar">
    <svg width="263" height="18" viewBox="0 0 263 18" aria-hidden="true">
      <circle cx="5" cy="-1" r="3" fill="#ccc"/>
      <rect x="12" y="6" width="2" height="7" fill="#aaa"/><rect x="16" y="6" width="2" height="7" fill="#aaa"/>
      <rect x="238" y="6" width="8" height="6" fill="none" stroke="#aaa"/><rect x="250" y="6" width="8" height="6" fill="none" stroke="#aaa"/>
    </svg>
  </div>
</div>
<p class="abs welcome-text">Sed ut perspiciatis, unde omnis iste natus error sit voluptatem accusantium doloremque laudantium, totam rem aperiam eaque ipsa, quae ab illo inventore veritatis et quasi architecto beatae vitae dicta sunt, explicabo. Nemo enim ipsam voluptatem, quia voluptas sit, aspernatur aut odit aut fugit, sed quia consequuntur magni dolores eos, qui ratione voluptatem sequi nesciunt, neque porro quisquam est, qui dolorem ipsum, quia dolor sit amet, consectetur, adipisci[ng] velit, sed quia non numquam [do] eius modi tempora inci[di]dunt, ut labore et dolore magnam aliquam quaerat voluptatem. Ut enim ad minima veniam, quis nostrum exercitationem ullam corporis suscipit laboriosam, nisi ut aliquid ex ea commodi consequatur?</p>

<!-- training -->
<h2 class="abs heading col-title" style="left:307px">Training &amp; Development</h2>
<div class="abs training-box">
  <div class="training-item">Leadership Training<svg width="12" height="14" aria-hidden="true"><path d="M0 0L12 7L0 14Z" fill="#000"/></svg></div>
  <div class="training-item">CPD<svg width="12" height="14" aria-hidden="true"><path d="M0 0L12 7L0 14Z" fill="#000"/></svg></div>
  <div class="training-item">School 2 School Support<svg width="12" height="14" aria-hidden="true"><path d="M0 0L12 7L0 14Z" fill="#000"/></svg></div>
  <div class="training-item">Research &amp; Development<svg width="12" height="14" aria-hidden="true"><path d="M0 0L12 7L0 14Z" fill="#000"/></svg></div>
  <div class="training-item">IT (School Direct)<svg width="12" height="14" aria-hidden="true"><path d="M0 0L12 7L0 14Z" fill="#000"/></svg></div>
</div>

<h2 class="abs heading" style="left:307px;top:686px;font-size:22px">News</h2>
<div class="abs news-box">
  <div class="news-item"><h3>Lorem ipsum dolor sit amet</h3><p>At vero eos et accusamus et iusto odio dignissimos ducimus, qui blanditiis praesentium voluptatum deleniti atque corrupti, quos dolores et quas molestias excepturi</p></div>
  <div class="news-item"><h3>Lorem ipsum dolor sit amet</h3><p>At vero eos et accusamus et iusto odio dignissimos ducimus, qui blanditiis praesentium voluptatum deleniti atque corrupti, quos dolores et quas molestias excepturi</p></div>
</div>

<!-- courses -->
<h2 class="abs heading col-title" style="left:605px">Latest Courses</h2>
<section class="abs courses-box">
  <div class="course"><h3>Want to deliver consistently ‘Outstanding Lessons?’</h3><p>Nam libero tempore, cum soluta nobis est eligendi optio, cumque nihil impedit, quo minus id, quod</p><div class="course-foot"><span class="places">6 places left</span><span class="book">Book</span></div></div>
  <div class="course"><h3>Want to deliver consistently ‘Outstanding Lessons?’</h3><p>Nam libero tempore, cum soluta nobis est eligendi optio, cumque nihil impedit, quo minus id, quod</p><div class="course-foot"><span class="places">6 places left</span><span class="book">Book</span></div></div>
  <div class="course"><h3>Want to deliver consistently ‘Outstanding Lessons?’</h3><p>Nam libero tempore, cum soluta nobis est eligendi optio, cumque nihil impedit, quo minus id, quod</p><div class="course-foot"><span class="places">6 places left</span><span class="book">Book</span></div></div>
  <div class="course-nav">
    <svg width="21" height="21" aria-label="Previous"><circle cx="10.5" cy="10.5" r="10.5" fill="var(--green-dark)"/><path d="M13 5.5L6.5 10.5L13 15.5Z" fill="#fff"/></svg>
    <svg width="21" height="21" aria-label="Next"><circle cx="10.5" cy="10.5" r="10.5" fill="var(--green-dark)"/><path d="M8 5.5L14.5 10.5L8 15.5Z" fill="#fff"/></svg>
  </div>
</section>

<!-- partners -->
<div class="abs partners" aria-label="Partner schools">
  <svg class="badge" style="left:28px;top:12px" width="40" height="48" aria-hidden="true"><path d="M26 0L10 24L26 48H36L20 24L36 0Z M14 0L0 24L14 48H22L8 24L22 0Z" fill="#666"/></svg>
  <svg class="badge" style="left:97px;top:5px" width="44" height="60" aria-hidden="true"><path d="M2 2H42V30Q42 50 22 58Q2 50 2 30Z" fill="#c9c9c9"/></svg>
  <svg class="badge" style="left:176px;top:5px" width="40" height="60" aria-hidden="true"><path d="M2 2H38V30Q38 50 20 58Q2 50 2 30Z" fill="#3a7a3a"/></svg>
  <div class="badge" style="left:246px;top:5px;width:62px;height:64px;background:#1e3fa8"></div>
  <svg class="badge" style="left:340px;top:5px" width="56" height="60" aria-hidden="true"><circle cx="28" cy="30" r="26" fill="#d6def0"/></svg>
  <div class="badge" style="left:422px;top:16px;width:90px;height:38px;background:#e8e8ec"></div>
  <svg class="badge" style="left:536px;top:5px" width="64" height="62" aria-hidden="true"><path d="M6 2H58V28Q58 50 32 60Q6 50 6 28Z" fill="#244f9a"/></svg>
  <svg class="badge" style="left:628px;top:5px" width="50" height="62" aria-hidden="true"><path d="M3 2H47V30Q47 52 25 60Q3 52 3 30Z" fill="#d9dde8"/></svg>
  <svg class="badge" style="left:710px;top:6px" width="74" height="60" aria-hidden="true"><ellipse cx="37" cy="30" rx="34" ry="26" fill="#ee5a2b"/></svg>
  <svg class="badge" style="left:825px;top:12px" width="40" height="48" aria-hidden="true"><path d="M4 0L20 24L4 48H14L30 24L14 0Z M18 0L32 24L18 48H26L40 24L26 0Z" fill="#666"/></svg>
</div>
<div class="abs partner-bar"></div>
<div class="abs partner-shadow"></div>

<!-- footer -->
<footer>
  <div class="abs footer-col" style="left:15px">Marlow Vale Teaching Alliance<br>Orchard Lane<br>Ashbridge<br>AB1 2CD<br>Tel: 01234 567890<br>email:info@marlowvaleteaching.example</div>
  <div class="abs footer-col" style="left:331px">About Us<br>Training &amp; Development<br>Benefits<br>Members<br>Calendar Events</div>
  <div class="abs footer-col" style="left:511px">Contact Us<br>News<br>Forum<br>Site Map</div>
  <div class="abs hub"><span class="hub-square"></span><span class="hub-name">Regional<br>Teaching<br>Hub</span></div>
  <div class="abs social">Chirp<br>Linkup</div>
  <div class="abs copyright">© Copyright 2013<br>Marlow Vale Teaching Alliance</div>
</footer>

</body>
</html>
```